Visitenkarten-Design für Sonnen-/Fensterschutz
Zielgruppe
KLW GmbH ist eine Firma, die Sonnenschutz und Fensterschutz anbieten.
'Ihr kompetenter Partner in Sachen Sonnenschutz- , Fenster- und Türtechnik. Sie erhalten echtes Handwerk aus dem Mühlviertel zu fairen Preisen.'
Unsere Zielgruppe sind Personen mit Haus, die am Land leben.
Firmenname: KLW GmbH
Slogan: Fenster & Sonnenschutz
Aufgabenstellung
Hier befindet sich das Logodesign: https://dx.qv/t-QwLpo7RbNs
Bitte ein schlichtes Design bereitstellen mit einer Dummy-Person:
Jonas Weidlinger + Telefonnummer + Email
Die finalen Daten bitte erst am Schluss berücksichtigen (für Gewinnerdesign)
Gerne auch hintern + vorne bedruckbar bereitstellen.

```html
<!DOCTYPE html>
<html lang="de">
<head>
<meta charset="utf-8">
<title>KLW GmbH – Visitenkarte</title>
<link rel="stylesheet" href="https://fonts.googleapis.com/css2?family=Open+Sans:wght@400;600&family=Poppins:wght@400;700&family=Oswald:wght@600&display=swap">
<style>
  :root {
    --stage: #58585a;
    --paper: #ffffff;
    --brand-orange: #ee7a1e;
    --brand-red: #e2361f;
    --brand-dark: #9e1c1c;
    --ink: #555558;
    --ink-soft: #6a6a6d;
    --ink-grey: #8a8a8d;
  }
  * { margin: 0; padding: 0; box-sizing: border-box; }
  html, body { width: 1200px; height: 1200px; overflow: hidden; }
  body { background: var(--stage); position: relative; font-family: "Poppins", sans-serif; }

  .card { position: absolute; width: 689px; height: 446px; background: var(--paper); overflow: hidden; }
  .card--front { left: 239px; top: 94px; }
  .card--back { left: 250px; top: 632px; }

  .brand { position: absolute; left: 318px; top: 44px; width: 340px; text-align: right; }
  .brand__name {
    font-family: "Poppins", sans-serif; font-weight: 700; font-size: 56px; line-height: 80px;
    color: var(--brand-red); letter-spacing: 1px; white-space: nowrap;
  }
  .brand__rule { height: 2px; background: var(--brand-red); margin-top: 4px; }
  .brand__slogan {
    font-family: "Oswald", sans-serif; font-weight: 600; font-size: 21px; line-height: 26px;
    color: var(--brand-dark); letter-spacing: 0.5px; margin-top: 2px; white-space: nowrap;
  }

  .person { position: absolute; left: 60px; top: 270px; width: 280px; text-align: center; font-family: "Open Sans", sans-serif; }
  .person__name { font-size: 26px; color: var(--ink); line-height: 34px; }
  .person__role { font-size: 19px; color: var(--ink); line-height: 28px; margin-top: 2px; }

  .contact { position: absolute; left: 398px; top: 220px; list-style: none; color: var(--ink-soft); font-size: 19px; line-height: 22px; }
  .contact__company { font-weight: 400; font-size: 16px; line-height: 20px; color: var(--ink-grey); margin-bottom: 10px; white-space: nowrap; }
  .contact__item { display: flex; align-items: flex-start; gap: 6px; margin-bottom: 13px; white-space: nowrap; }
  .contact__item svg { flex: 0 0 22px; width: 22px; height: 22px; margin-top: 1px; }
  .contact__item--address { margin-bottom: 16px; }

  .stripes { position: absolute; left: 0; top: 378px; width: 689px; height: 50px; }

  .back-brand {
    position: absolute; inset: 0; display: flex; align-items: center; justify-content: center;
    font-family: "Poppins", sans-serif; font-weight: 700; font-size: 96px; color: var(--brand-red); letter-spacing: 2px;
    white-space: nowrap;
  }
</style>
</head>
<body>

<section class="card card--front" aria-label="Vorderseite">
  <div class="brand">
    <div class="brand__name">KLW GmbH</div>
    <div class="brand__rule"></div>
    <div class="brand__slogan">FENSTER &amp; SONNENSCHUTZ</div>
  </div>

  <div class="person">
    <p class="person__name">Jonas Weidlinger</p>
    <p class="person__role">Geschäftsführer</p>
  </div>

  <ul class="contact">
    <li class="contact__company">KLW GmbH</li>
    <li class="contact__item contact__item--address">
      <svg viewBox="0 0 24 24" aria-hidden="true"><path d="M2 3 L22 12 L2 21 L7 12 Z" fill="var(--brand-red)"/></svg>
      <span>Am Lindenhang 7-9<br>30519 Hannover</span>
    </li>
    <li class="contact__item">
      <svg viewBox="0 0 24 24" aria-hidden="true"><path d="M6 2 L10 7 L8 10 C9 13 11 15 14 16 L17 14 L22 18 L19 22 C10 21 3 14 2 5 Z" fill="var(--brand-red)"/></svg>
      <span>+49 160 482 3917</span>
    </li>
    <li class="contact__item">
      <svg viewBox="0 0 24 24" aria-hidden="true"><rect x="2" y="5" width="20" height="15" rx="2" fill="var(--brand-red)"/><path d="M3 7 L12 14 L21 7" stroke="#fff" stroke-width="2" fill="none"/></svg>
      <span>+49 160 482 3917</span>
    </li>
  </ul>

  <svg class="stripes" viewBox="0 0 689 50" aria-hidden="true">
    <defs>
      <linearGradient id="stripeFade" x1="0" x2="1" y1="0" y2="0">
        <stop offset="0" stop-color="#e2361f"/>
        <stop offset="0.5" stop-color="#ee6a1e"/>
        <stop offset="1" stop-color="#e2361f"/>
      </linearGradient>
    </defs>
    <rect x="0" y="1" width="689" height="2" fill="url(#stripeFade)"/>
    <rect x="0" y="8" width="689" height="8" fill="url(#stripeFade)"/>
    <rect x="0" y="24" width="689" height="9" fill="url(#stripeFade)"/>
    <rect x="0" y="42" width="689" height="2" fill="url(#stripeFade)"/>
  </svg>
</section>

<section class="card card--back" aria-label="Rückseite">
  <div class="back-brand">KLW GmbH</div>
</section>

</body>
</html>
```